Lantern Petals Website v.1 - attract floral shop franchisees

I need a simple information website for my new business. We are a franchisor of flower shops. The overall purpose of the website is to promote the company and the service, especially to potential franchisees and retailers. Only about 4 pages are required including homepage, About, For Supermarkets, For Franchisees, and Contact. No special functions are required except the site will have two separate inquiry forms that must be filled out online and submitted via automated email. Similarly, an email form should be linked from the Contact page. I have a logo and business cards designed by ArtMingle, and I would like the site to have a consistent color scheme and style. The key to design will be to express the joy and love associated with flowers and floral bouquets.
IMPORTANT - I will be exporting the website design to Wordpress CMS in a site hosted by HostNimbus. For smooth integration into WordPress hosted by HostNimbus, the designer should build the site using a WordPress-friendly format. Ideally, they should use HTML, CSS, and PHP. Creating a custom theme or using a page builder that exports to WordPress-compatible files is best. This ensures the site can be easily imported and managed within WordPress.

Target Market(s)

Potential franchisees (existing florists or creative types who might like to own a floral business) and supermarkets who might want us to run their floral department

Industry/Entity Type

Floral retailing

Requirements
Must have
• A brand theme that is beautiful, consistent throughout and builds on the logo design
Nice to have
• Show gender and ethnic diversity in customers and florists. Pictures of happy florists (for franchisees) and pictures of amazing floral department displays (for supermarkets)

```html
<!DOCTYPE html>
<html lang="en">
<head>
<meta charset="utf-8">
<title>Lantern Petals – Website Homepage</title>
<link href="https://fonts.googleapis.com/css2?family=Great+Vibes&family=Roboto:wght@400;500;700&display=swap" rel="stylesheet">
<style>
:root{
  --board:#e4e4e4;
  --white:#ffffff;
  --orange:#f0961c;
  --green:#12913f;
  --green-dark:#0c7a33;
  --ink:#333333;
  --muted:#6b6b6b;
  --grey-panel:#f3f3f3;
  --black:#050505;
}
*{box-sizing:border-box;margin:0;padding:0}
html,body{width:1131px;height:1200px;overflow:hidden;background:var(--board);font-family:"Roboto",sans-serif;color:var(--ink)}
.board{position:relative;width:1131px;height:1200px}
.page{position:absolute;top:52px;width:301px;height:1093px;background:var(--white);overflow:hidden;box-shadow:0 1px 4px rgba(0,0,0,.12)}
.page--one{left:67px}.page--two{left:415px}.page--three{left:763px}
.script{font-family:"Great Vibes",cursive;font-weight:400}
.btn{display:inline-flex;align-items:center;gap:2px;height:10px;padding:0 6px;border-radius:6px;font-size:3.4px;font-weight:700;color:var(--white);letter-spacing:.1px}
.btn::after{content:"";width:3px;height:3px;border-radius:50%;background:var(--white)}
.btn--orange{background:var(--orange)}
.btn--green{background:var(--green)}
.btn--outline{border:.6px solid var(--white)}
.hex{clip-path:polygon(25% 0,75% 0,100% 50%,75% 100%,25% 100%,0 50%)}
.deco{position:absolute;border-radius:50%;opacity:.55}
p.copy{font-size:3.2px;line-height:6.4px;color:var(--muted);text-align:justify}

/* header */
.site-header{position:relative;height:27px}
.brand{position:absolute;left:27px;top:8px;display:flex;align-items:center;gap:3px}
.brand__dot{width:8px;height:8px;border-radius:50%;background:var(--orange)}
.brand__name{font-size:7px;font-weight:500;color:var(--orange)}
.header-contact{position:absolute;right:27px;top:4px;display:flex;align-items:center;gap:3px}
.social{width:8px;height:8px;border-radius:50%;border:.7px solid var(--green)}
.call{display:flex;align-items:center;gap:2px;margin-left:3px}
.call__icon{width:8px;height:8px;border-radius:50%;background:var(--orange);display:flex;align-items:center;justify-content:center}
.call__text{font-size:3px;line-height:3.8px}
.call__text b{font-size:3.6px}
.main-nav{position:absolute;right:28px;top:18px;display:flex;gap:9px;font-size:3.6px;font-weight:500}

/* hero */
.hero{position:relative;height:200px}
.hero__photo{position:absolute;inset:0 0 12px 0;background:linear-gradient(100deg,#b5234e 0%,#e0508c 18%,#6d7a3b 35%,#caa98a 50%,#3c5f98 62%,#d8453c 80%,#8b3a2d 100%)}
.hero__band{position:absolute;left:74px;top:55px;width:152px;height:76px;background:rgba(40,30,20,.45);text-align:center;color:var(--white)}
.hero__welcome{font-size:12px;margin-top:6px}
.hero__title{font-size:22px;line-height:24px}
.hero__band .btn{margin-top:4px}
.wave{position:absolute;left:0;width:301px}

/* about */
.about{position:relative;height:165px}
.about__cluster{position:absolute;left:38px;top:10px;width:110px;height:130px}
.about__cluster .hex{position:absolute;width:42px;height:38px}
.about__text{position:absolute;left:170px;top:28px;width:103px}
.section-title{font-size:13px;color:var(--ink);margin-bottom:4px}
.about__text .btn{margin-top:6px}
.about__pair{position:absolute;left:38px;top:14px;width:120px;height:120px}
.about__pair .hex--lg{position:absolute;left:0;top:0;width:94px;height:86px}
.about__pair .hex--sm{position:absolute;left:58px;top:52px;width:66px;height:60px}

/* supermarkets */
.supermarkets{position:relative;height:133px;background:var(--grey-panel)}
.supermarkets__text{position:absolute;left:28px;top:12px;width:106px}
.supermarkets__text .btn{margin-top:6px}
.supermarkets__photo{position:absolute;right:0;top:0;width:147px;height:133px;background:radial-gradient(circle at 50% 55%,#e98aa0 0%,#b6c95a 30%,#d9c6b0 60%,#e9eef2 100%)}

/* franchisees */
.franchisees{position:relative;height:157px}
.franchisees__hex-frame{position:absolute;left:40px;top:28px;width:112px;height:98px;background:#c9a24a}
.franchisees__hex{position:absolute;left:41.5px;top:29.5px;width:109px;height:95px;background:radial-gradient(circle at 45% 50%,#f5c2b0 0%,#e8e8e0 40%,#8fae8a 75%,#5b6a5a 100%)}
.franchisees__text{position:absolute;left:165px;top:28px;width:110px}
.franchisees__text .btn{margin-top:6px}

/* contact */
.contact{position:relative;height:121px;background:var(--green);text-align:center;color:var(--white)}
.contact__title{font-size:14px;padding-top:12px;color:var(--white)}
.contact__copy{font-size:3.3px;line-height:6.4px;width:196px;margin:3px auto 0}
.contact__actions{display:flex;justify-content:center;gap:3px;margin-top:6px}

/* gallery */
.gallery{position:relative;height:170px}
.gallery__title{text-align:center;font-size:13px;padding-top:16px}
.gallery__row{position:absolute;display:flex;gap:5px}
.gallery__row--top{left:30px;top:40px}
.gallery__row--bottom{left:61px;top:99px}
.gallery__row .hex{width:57px;height:50px}

/* footer */
.site-footer{position:relative;height:109px;background:var(--black);color:var(--white)}
.footer__brand{position:absolute;left:28px;top:36px;display:flex;align-items:center;gap:3px}
.footer__brand .brand__dot{width:10px;height:10px}
.footer__brand .brand__name{font-size:8px}
.footer__col{position:absolute;top:36px;font-size:3.2px}
.footer__col h4{font-size:3.4px;font-weight:700;margin-bottom:5px}
.footer__col li{list-style:none;margin-bottom:4px}
.footer__col--links{left:93px}
.footer__col--contact{left:144px;width:55px}
.footer__col--subscribe{left:208px;width:66px}
.contact-line{display:flex;gap:3px;align-items:flex-start;margin-bottom:4px;line-height:3.8px}
.contact-line i{flex:none;width:4px;height:4px;border-radius:50%;background:#555}
.subscribe-field{display:flex;margin-top:4px;height:10px;border-radius:5px;background:var(--white);overflow:hidden;width:64px}
.subscribe-field span{flex:1;color:#888;font-size:2.8px;padding:3.5px 5px}
.subscribe-field b{width:11px;background:var(--green)}
.footer__social{display:flex;gap:3px;margin-top:5px}
.footer__social i{width:7px;height:7px;border-radius:50%;border:.6px solid var(--white)}
.footer__bar{position:absolute;left:0;bottom:0;width:301px;height:11px;background:var(--orange);font-size:3.2px;color:var(--white);text-align:center;line-height:11px}
.footer__bar + .footer__spacer{display:none}
</style>
</head>
<body>
<div class="board">

<!-- PAGE 1 -->
<section class="page page--one">
  <header class="site-header">
    <div class="brand"><span class="brand__dot"></span><span class="brand__name">Lantern Petals</span></div>
    <div class="header-contact">
      <span class="social"></span><span class="social"></span>
      <div class="call"><span class="call__icon"><svg width="4" height="4" viewBox="0 0 10 10"><path d="M2 1l2 2-1 1.5a6 6 0 002.5 2.5L7 6l2 2-1.5 1.5C4 9 1 6 .5 2z" fill="#fff"/></svg></span><span class="call__text">Call Us<br><b>+ 1.555.010.2040</b></span></div>
    </div>
    <nav class="main-nav"><span>HOME</span><span>ABOUT</span><span>FOR SUPERMARKETS</span><span>FOR FRANCHISEES</span><span>CONTACT</span></nav>
  </header>
  <div class="hero">
    <div class="hero__photo" role="img" aria-label="Smiling florist arranging a vase of flowers in a colourful flower shop"></div>
    <div class="hero__band"><div class="hero__welcome script">Welcome To</div><div class="hero__title script">Lantern Petals</div><span class="btn btn--orange">GET STARTED</span></div>
    <svg class="wave" style="bottom:0" height="45" viewBox="0 0 301 45"><path d="M0 12 C70 -2 150 20 210 30 C250 36 280 30 301 22 L301 45 L0 45Z" fill="#f0961c"/><path d="M0 20 C70 6 150 26 210 34 C250 40 280 34 301 26 L301 45 L0 45Z" fill="#12913f"/><path d="M0 27 C70 14 150 32 210 38 C250 42 280 38 301 30 L301 45 L0 45Z" fill="#fff"/></svg>
  </div>
  <div class="about">
    <div class="deco" style="left:4px;top:22px;width:22px;height:60px;background:linear-gradient(#12913f,#f0961c)" role="img" aria-label="Decorative bee illustration"></div>
    <div class="about__cluster">
      <div class="hex" style="left:0;top:18px;background:linear-gradient(#4a6a3e,#2f3b2a)" role="img" aria-label="Flower shop interior"></div>
      <div class="hex" style="left:38px;top:0;background:linear-gradient(#a9c98f,#6f8f5a)" role="img" aria-label="Florist holding flowers"></div>
      <div class="hex" style="left:72px;top:24px;background:linear-gradient(#c9d6c0,#7a9a74)" role="img" aria-label="Florist at work"></div>
      <div class="hex" style="left:0;top:56px;background:linear-gradient(#c0394a,#6e2a2a)" role="img" aria-label="Florist among red blooms"></div>
      <div class="hex" style="left:64px;top:64px;background:linear-gradient(#d7a16a,#8a4a32)" role="img" aria-label="Florist in shop"></div>
      <div class="hex" style="left:30px;top:80px;background:linear-gradient(#e67e92,#5b7a3c)" role="img" aria-label="Smiling florist"></div>
    </div>
    <div class="about__text">
      <h2 class="section-title script">About Us</h2>
      <p class="copy">Lantern Petals operates in partnership with Frostline Group, the leading franchisor of sushi stations and pre-packaged fruit &amp; vegetable departments to supermarkets across the United States and United Kingdom. Lantern Petals' combination of floral and supermarket franchising expertise guarantees that consumers, franchisees and supermarket partners each receive exceptional service and value.</p>
      <span class="btn btn--orange">LEARN MORE</span>
    </div>
    <div class="deco" style="right:6px;top:96px;width:44px;height:60px;background:linear-gradient(#f0961c,#12913f)" role="img" aria-label="Decorative honeycomb flower illustration"></div>
    <svg class="wave" style="bottom:-2px" height="30" viewBox="0 0 301 30"><path d="M0 22 C60 0 150 6 220 14 C260 18 285 10 301 0 L301 30 L0 30Z" fill="#f3f3f3"/><path d="M60 6 C140 0 220 20 301 4 L301 12 C220 28 140 10 60 6Z" fill="#f0961c"/><path d="M100 6 C170 4 240 16 301 0 L301 4 C240 20 170 8 100 6Z" fill="#12913f"/></svg>
  </div>
  <div class="supermarkets">
    <div class="supermarkets__text">
      <h2 class="section-title script">For Supermarkets</h2>
      <p class="copy">Lantern Petals works with some of the country's largest and most progressive supermarkets to provide franchisee ownership and operation of their strategically important floral departments. Supermarkets find that Lantern Petals is able to improve their financial outcomes, provide attentive customer service and satisfaction, and lift the quality of the entire store environment.</p>
      <p class="copy">Lantern Petals works with some of the country's largest and most progressive supermarkets to provide franchisee ownership and operation of their strategically important floral departments.</p>
      <span class="btn btn--green">LEARN MORE</span>
    </div>
    <div class="supermarkets__photo" role="img" aria-label="Hands holding a large mixed bouquet of roses and greenery"></div>
  </div>
  <div class="franchisees">
    <div class="deco" style="left:8px;top:50px;width:24px;height:90px;background:linear-gradient(#12913f,#f0961c)" role="img" aria-label="Decorative bee illustration"></div>
    <div class="franchisees__hex-frame hex"></div>
    <div class="franchisees__hex hex" role="img" aria-label="Pastel bouquet of roses and carnations wrapped in paper"></div>
    <div class="franchisees__text">
      <h2 class="section-title script">For Franchisees</h2>
      <p class="copy">Lantern Petals brings the best of professional florists and supermarkets together for the benefit of consumers. It supports a national network of owner-operator franchisees, who in many cases are multi-site professional florists, with comprehensive services to enhance franchise profitability. Lantern Petals works with some of the country's largest and most progressive supermarkets to provide franchisee ownership and operation of their strategically important floral departments</p>
      <span class="btn btn--orange">LEARN MORE</span>
    </div>
  </div>
  <div class="contact">
    <h2 class="contact__title script">Contact Us</h2>
    <p class="contact__copy">Lorem ipsum dolor sit ameted consectetur adipiscing elited sed do eiusmod tempor incididunt ut labore dolore magna aliqua Uted enim ad minim veniam, quis nostrud exercitation ullamco laboris nisi ut aliquip ex ea commodo consequat. Duis aute irure dolor in reprehenderit in voluptate velit esse cillum dolore</p>
    <div class="contact__actions"><span class="btn btn--orange">NEW FLORIST FRANCHISE INQUIRY</span><span class="btn btn--outline">PROFESSIONAL FLORIST FRANCHISE INQUIRY</span></div>
    <svg class="wave" style="bottom:0" height="34" viewBox="0 0 301 34"><path d="M0 18 C50 4 110 6 170 16 C230 26 270 20 301 10 L301 34 L0 34Z" fill="#f0961c"/><path d="M0 24 C50 10 110 12 170 22 C230 30 270 26 301 16 L301 34 L0 34Z" fill="#12913f"/><path d="M0 30 C50 16 110 18 170 27 C230 34 270 30 301 22 L301 34 L0 34Z" fill="#fff"/></svg>
  </div>
  <div class="gallery">
    <h2 class="gallery__title script">Our Gallery</h2>
    <div class="gallery__row gallery__row--top">
      <div class="hex" style="background:linear-gradient(#6f8a4a,#5a3a2a)" role="img" aria-label="Florist standing in shop"></div>
      <div class="hex" style="background:linear-gradient(#d86a9a,#4e6e3a)" role="img" aria-label="Florist holding bouquet"></div>
      <div class="hex" style="background:linear-gradient(#f0b8a0,#d84a6a)" role="img" aria-label="Florist with pink flowers"></div>
      <div class="hex" style="background:linear-gradient(#5a6a3a,#a03a3a)" role="img" aria-label="Florists arranging flowers"></div>
    </div>
    <div class="gallery__row gallery__row--bottom">
      <div class="hex" style="background:linear-gradient(#d8b0a0,#8a5a3a)" role="img" aria-label="Florist at counter"></div>
      <div class="hex" style="background:linear-gradient(#b0205a,#e86aa0)" role="img" aria-label="Pink flower box arrangement"></div>
      <div class="hex" style="background:linear-gradient(#e8d8d0,#5a6a4a)" role="img" aria-label="Hands arranging protea bouquet"></div>
    </div>
    <div class="deco" style="left:8px;top:110px;width:40px;height:56px;background:linear-gradient(#f0961c,#12913f)" role="img" aria-label="Decorative honeycomb flower illustration"></div>
    <div class="deco" style="right:4px;top:76px;width:26px;height:80px;background:linear-gradient(#12913f,#f0961c)" role="img" aria-label="Decorative bee illustration"></div>
  </div>
  <footer class="site-footer">
    <svg class="wave" style="top:-12px" height="40" viewBox="0 0 301 40"><path d="M0 0 L301 0 L301 6 C250 24 150 26 90 12 C50 4 20 6 0 12Z" fill="#fff"/><path d="M0 12 C20 6 50 4 90 12 C150 26 250 24 301 6 L301 14 C250 32 150 32 90 18 C50 10 20 12 0 18Z" fill="#f0961c"/><path d="M0 18 C20 12 50 10 90 18 C150 32 250 32 301 14 L301 18 C250 36 150 36 90 22 C50 14 20 16 0 22Z" fill="#12913f"/></svg>
    <div class="footer__brand"><span class="brand__dot"></span><span class="brand__name">Lantern Petals</span></div>
    <div class="footer__col footer__col--links"><h4>QUICK LINKS</h4><ul><li>» &nbsp;Home</li><li>» &nbsp;About</li><li>» &nbsp;For Supermarkets</li><li>» &nbsp;For Franchisees</li><li>» &nbsp;Contact</li></ul></div>
    <div class="footer__col footer__col--contact"><h4>CONTACT US</h4><div class="contact-line"><i></i><b>+ 1.555.010.2040</b></div><div class="contact-line"><i></i>hello@lanternpetals.com</div><div class="contact-line"><i></i>114 Orchard Lane suite four near the market</div><div class="contact-line"><i></i><u>View Other Locations</u></div></div>
    <div class="footer__col footer__col--subscribe"><h4>SUBSCRIBE NOW</h4><p>Sign up to our newsletter and stay up to date</p><div class="subscribe-field"><span>Email Address</span><b></b></div><div class="footer__social"><i></i><i></i></div></div>
    <div class="footer__bar">© 2024 Lantern Petals. All Rights Reserved</div>
  </footer>
</section>

<!-- PAGE 2 -->
<section class="page page--two">
  <header class="site-header">
    <div class="brand"><span class="brand__dot"></span><span class="brand__name">Lantern Petals</span></div>
    <div class="header-contact">
      <span class="social"></span><span class="social"></span>
      <div class="call"><span class="call__icon"><svg width="4" height="4" viewBox="0 0 10 10"><path d="M2 1l2 2-1 1.5a6 6 0 002.5 2.5L7 6l2 2-1.5 1.5C4 9 1 6 .5 2z" fill="#fff"/></svg></span><span class="call__text">Call Us<br><b>+ 1.555.010.2040</b></span></div>
    </div>
    <nav class="main-nav"><span>HOME</span><span>ABOUT</span><span>FOR SUPERMARKETS</span><span>FOR FRANCHISEES</span><span>CONTACT</span></nav>
  </header>
  <div class="hero">
    <div class="hero__photo" role="img" aria-label="Smiling florist arranging a vase of flowers in a colourful flower shop"></div>
    <div class="hero__band"><div class="hero__welcome script">Welcome To</div><div class="hero__title script">Lantern Petals</div><span class="btn btn--orange">GET STARTED</span></div>
    <svg class="wave" style="bottom:0" height="45" viewBox="0 0 301 45"><path d="M0 12 C70 -2 150 20 210 30 C250 36 280 30 301 22 L301 45 L0 45Z" fill="#f0961c"/><path d="M0 20 C70 6 150 26 210 34 C250 40 280 34 301 26 L301 45 L0 45Z" fill="#12913f"/><path d="M0 27 C70 14 150 32 210 38 C250 42 280 38 301 30 L301 45 L0 45Z" fill="#fff"/></svg>
  </div>
  <div class="about">
    <div class="deco" style="left:4px;top:22px;width:22px;height:60px;background:linear-gradient(#12913f,#f0961c)" role="img" aria-label="Decorative bee illustration"></div>
    <div class="about__cluster" style="top:0">
      <div class="hex" style="left:0;top:18px;background:linear-gradient(#4a6a3e,#2f3b2a)" role="img" aria-label="Flower shop interior"></div>
      <div class="hex" style="left:38px;top:0;background:linear-gradient(#a9c98f,#6f8f5a)" role="img" aria-label="Florist holding flowers"></div>
      <div class="hex" style="left:72px;top:36px;background:linear-gradient(#c9d6c0,#7a9a74)" role="img" aria-label="Florist at work"></div>
      <div class="hex" style="left:0;top:60px;background:linear-gradient(#c0394a,#6e2a2a)" role="img" aria-label="Florist among red blooms"></div>
      <div class="hex" style="left:64px;top:76px;background:linear-gradient(#d7a16a,#8a4a32)" role="img" aria-label="Florist in shop"></div>
      <div class="hex" style="left:30px;top:90px;background:linear-gradient(#e67e92,#5b7a3c)" role="img" aria-label="Smiling florist"></div>
    </div>
    <div class="about__text">
      <h2 class="section-title script">About Us</h2>
      <p class="copy">Lantern Petals operates in partnership with Frostline Group, the leading franchisor of sushi stations and pre-packaged fruit &amp; vegetable departments to supermarkets across the United States and United Kingdom. Lantern Petals' combination of floral and supermarket franchising expertise guarantees that consumers, franchisees and supermarket partners each receive exceptional service and value.</p>
      <span class="btn btn--orange">LEARN MORE</span>
    </div>
    <div class="deco" style="right:6px;top:96px;width:44px;height:60px;background:linear-gradient(#f0961c,#12913f)" role="img" aria-label="Decorative honeycomb flower illustration"></div>
    <svg class="wave" style="bottom:-2px" height="30" viewBox="0 0 301 30"><path d="M0 22 C60 0 150 6 220 14 C260 18 285 10 301 0 L301 30 L0 30Z" fill="#f3f3f3"/><path d="M60 6 C140 0 220 20 301 4 L301 12 C220 28 140 10 60 6Z" fill="#f0961c"/><path d="M100 6 C170 4 240 16 301 0 L301 4 C240 20 170 8 100 6Z" fill="#12913f"/></svg>
  </div>
  <div class="supermarkets">
    <div class="supermarkets__text">
      <h2 class="section-title script">For Supermarkets</h2>
      <p class="copy">Lantern Petals works with some of the country's largest and most progressive supermarkets to provide franchisee ownership and operation of their strategically important floral departments. Supermarkets find that Lantern Petals is able to improve their financial outcomes, provide attentive customer service and satisfaction, and lift the quality of the entire store environment.</p>
      <p class="copy">Lantern Petals works with some of the country's largest and most progressive supermarkets to provide franchisee ownership and operation of their strategically important floral departments.</p>
      <span class="btn btn--green">LEARN MORE</span>
    </div>
    <div class="supermarkets__photo" role="img" aria-label="Hands holding a large mixed bouquet of roses and greenery"></div>
  </div>
  <div class="franchisees">
    <div class="deco" style="left:8px;top:50px;width:24px;height:90px;background:linear-gradient(#12913f,#f0961c)" role="img" aria-label="Decorative bee illustration"></div>
    <div class="franchisees__hex-frame hex"></div>
    <div class="franchisees__hex hex" role="img" aria-label="Pastel bouquet of roses and carnations wrapped in paper"></div>
    <div class="franchisees__text">
      <h2 class="section-title script">For Franchisees</h2>
      <p class="copy">Lantern Petals brings the best of professional florists and supermarkets together for the benefit of consumers. It supports a national network of owner-operator franchisees, who in many cases are multi-site professional florists, with comprehensive services to enhance franchise profitability. Lantern Petals works with some of the country's largest and most progressive supermarkets to provide franchisee ownership and operation of their strategically important floral departments</p>
      <span class="btn btn--orange">LEARN MORE</span>
    </div>
  </div>
  <div class="contact">
    <h2 class="contact__title script">Contact Us</h2>
    <p class="contact__copy">Lorem ipsum dolor sit ameted consectetur adipiscing elited sed do eiusmod tempor incididunt ut labore dolore magna aliqua Uted enim ad minim veniam, quis nostrud exercitation ullamco laboris nisi ut aliquip ex ea commodo consequat. Duis aute irure dolor in reprehenderit in voluptate velit esse cillum dolore</p>
    <div class="contact__actions"><span class="btn btn--orange">NEW FLORIST FRANCHISE INQUIRY</span><span class="btn btn--outline">PROFESSIONAL FLORIST FRANCHISE INQUIRY</span></div>
    <svg class="wave" style="bottom:0" height="34" viewBox="0 0 301 34"><path d="M0 18 C50 4 110 6 170 16 C230 26 270 20 301 10 L301 34 L0 34Z" fill="#f0961c"/><path d="M0 24 C50 10 110 12 170 22 C230 30 270 26 301 16 L301 34 L0 34Z" fill="#12913f"/><path d="M0 30 C50 16 110 18 170 27 C230 34 270 30 301 22 L301 34 L0 34Z" fill="#fff"/></svg>
  </div>
  <div class="gallery">
    <h2 class="gallery__title script">Our Gallery</h2>
    <div class="gallery__row gallery__row--top">
      <div class="hex" style="background:linear-gradient(#6f8a4a,#5a3a2a)" role="img" aria-label="Florist standing in shop"></div>
      <div class="hex" style="background:linear-gradient(#d86a9a,#4e6e3a)" role="img" aria-label="Florist holding bouquet"></div>
      <div class="hex" style="background:linear-gradient(#f0b8a0,#d84a6a)" role="img" aria-label="Florist with pink flowers"></div>
      <div class="hex" style="background:linear-gradient(#5a6a3a,#a03a3a)" role="img" aria-label="Florists arranging flowers"></div>
    </div>
    <div class="gallery__row gallery__row--bottom">
      <div class="hex" style="background:linear-gradient(#d8b0a0,#8a5a3a)" role="img" aria-label="Florist at counter"></div>
      <div class="hex" style="background:linear-gradient(#b0205a,#e86aa0)" role="img" aria-label="Pink flower box arrangement"></div>
      <div class="hex" style="background:linear-gradient(#e8d8d0,#5a6a4a)" role="img" aria-label="Hands arranging protea bouquet"></div>
    </div>
    <div class="deco" style="left:8px;top:110px;width:40px;height:56px;background:linear-gradient(#f0961c,#12913f)" role="img" aria-label="Decorative honeycomb flower illustration"></div>
    <div class="deco" style="right:4px;top:76px;width:26px;height:80px;background:linear-gradient(#12913f,#f0961c)" role="img" aria-label="Decorative bee illustration"></div>
  </div>
  <footer class="site-footer">
    <svg class="wave" style="top:-12px" height="40" viewBox="0 0 301 40"><path d="M0 0 L301 0 L301 6 C250 24 150 26 90 12 C50 4 20 6 0 12Z" fill="#fff"/><path d="M0 12 C20 6 50 4 90 12 C150 26 250 24 301 6 L301 14 C250 32 150 32 90 18 C50 10 20 12 0 18Z" fill="#f0961c"/><path d="M0 18 C20 12 50 10 90 18 C150 32 250 32 301 14 L301 18 C250 36 150 36 90 22 C50 14 20 16 0 22Z" fill="#12913f"/></svg>
    <div class="footer__brand"><span class="brand__dot"></span><span class="brand__name">Lantern Petals</span></div>
    <div class="footer__col footer__col--links"><h4>QUICK LINKS</h4><ul><li>» &nbsp;Home</li><li>» &nbsp;About</li><li>» &nbsp;For Supermarkets</li><li>» &nbsp;For Franchisees</li><li>» &nbsp;Contact</li></ul></div>
    <div class="footer__col footer__col--contact"><h4>CONTACT US</h4><div class="contact-line"><i></i><b>+ 1.555.010.2040</b></div><div class="contact-line"><i></i>hello@lanternpetals.com</div><div class="contact-line"><i></i>114 Orchard Lane suite four near the market</div><div class="contact-line"><i></i><u>View Other Locations</u></div></div>
    <div class="footer__col footer__col--subscribe"><h4>SUBSCRIBE NOW</h4><p>Sign up to our newsletter and stay up to date</p><div class="subscribe-field"><span>Email Address</span><b></b></div><div class="footer__social"><i></i><i></i></div></div>
    <div class="footer__bar">© 2024 Lantern Petals. All Rights Reserved</div>
  </footer>
</section>

<!-- PAGE 3 -->
<section class="page page--three">
  <header class="site-header">
    <div class="brand"><span class="brand__dot"></span><span class="brand__name">Lantern Petals</span></div>
    <div class="header-contact">
      <span class="social"></span><span class="social"></span>
      <div class="call"><span class="call__icon"><svg width="4" height="4" viewBox="0 0 10 10"><path d="M2 1l2 2-1 1.5a6 6 0 002.5 2.5L7 6l2 2-1.5 1.5C4 9 1 6 .5 2z" fill="#fff"/></svg></span><span class="call__text">Call Us<br><b>+ 1.555.010.2040</b></span></div>
    </div>
    <nav class="main-nav"><span>HOME</span><span>ABOUT</span><span>FOR SUPERMARKETS</span><span>FOR FRANCHISEES</span><span>CONTACT</span></nav>
  </header>
  <div class="hero">
    <div class="hero__photo" role="img" aria-label="Smiling florist arranging a vase of flowers in a colourful flower shop"></div>
    <div class="hero__band"><div class="hero__welcome script">Welcome To</div><div class="hero__title script">Lantern Petals</div><span class="btn btn--orange">GET STARTED</span></div>
    <svg class="wave" style="bottom:0" height="45" viewBox="0 0 301 45"><path d="M0 12 C70 -2 150 20 210 30 C250 36 280 30 301 22 L301 45 L0 45Z" fill="#f0961c"/><path d="M0 20 C70 6 150 26 210 34 C250 40 280 34 301 26 L301 45 L0 45Z" fill="#12913f"/><path d="M0 27 C70 14 150 32 210 38 C250 42 280 38 301 30 L301 45 L0 45Z" fill="#fff"/></svg>
  </div>
  <div class="about">
    <div class="deco" style="left:4px;top:22px;width:22px;height:60px;background:linear-gradient(#12913f,#f0961c)" role="img" aria-label="Decorative bee illustration"></div>
    <div class="about__pair">
      <div class="hex hex--lg" style="background:linear-gradient(160deg,#e8ecf0,#8fa7c8 55%,#b89ac8)" role="img" aria-label="Florist on the phone beside a bouquet"></div>
      <div class="hex hex--sm" style="background:linear-gradient(#3b6fc0,#f0e2a0 55%,#e89a30)" role="img" aria-label="Field of daisies and wildflowers"></div>
    </div>
    <div class="about__text" style="top:24px">
      <h2 class="section-title script">About Us</h2>
      <p class="copy">Lantern Petals operates in partnership with Frostline Group, the leading franchisor of sushi stations and pre-packaged fruit &amp; vegetable departments to supermarkets across the United States and United Kingdom. Lantern Petals' combination of floral and supermarket franchising expertise guarantees that consumers, franchisees and supermarket partners each receive exceptional service and value.</p>
      <span class="btn btn--orange">LEARN MORE</span>
    </div>
    <div class="deco" style="right:6px;top:96px;width:44px;height:60px;background:linear-gradient(#f0961c,#12913f)" role="img" aria-label="Decorative honeycomb flower illustration"></div>
    <svg class="wave" style="bottom:-2px" height="30" viewBox="0 0 301 30"><path d="M0 22 C60 0 150 6 220 14 C260 18 285 10 301 0 L301 30 L0 30Z" fill="#f3f3f3"/><path d="M60 6 C140 0 220 20 301 4 L301 12 C220 28 140 10 60 6Z" fill="#f0961c"/><path d="M100 6 C170 4 240 16 301 0 L301 4 C240 20 170 8 100 6Z" fill="#12913f"/></svg>
  </div>
  <div class="supermarkets">
    <div class="supermarkets__text">
      <h2 class="section-title script">For Supermarkets</h2>
      <p class="copy">Lantern Petals works with some of the country's largest and most progressive supermarkets to provide franchisee ownership and operation of their strategically important floral departments. Supermarkets find that Lantern Petals is able to improve their financial outcomes, provide attentive customer service and satisfaction, and lift the quality of the entire store environment.</p>
      <p class="copy">Lantern Petals works with some of the country's largest and most progressive supermarkets to provide franchisee ownership and operation of their strategically important floral departments.</p>
      <span class="btn btn--green">LEARN MORE</span>
    </div>
    <div class="supermarkets__photo" role="img" aria-label="Hands holding a large mixed bouquet of roses and greenery"></div>
  </div>
  <div class="franchisees">
    <div class="deco" style="left:8px;top:50px;width:24px;height:90px;background:linear-gradient(#12913f,#f0961c)" role="img" aria-label="Decorative bee illustration"></div>
    <div class="franchisees__hex-frame hex"></div>
    <div class="franchisees__hex hex" role="img" aria-label="Pastel bouquet of roses and carnations wrapped in paper"></div>
    <div class="franchisees__text">
      <h2 class="section-title script">For Franchisees</h2>
      <p class="copy">Lantern Petals brings the best of professional florists and supermarkets together for the benefit of consumers. It supports a national network of owner-operator franchisees, who in many cases are multi-site professional florists, with comprehensive services to enhance franchise profitability. Lantern Petals works with some of the country's largest and most progressive supermarkets to provide franchisee ownership and operation of their strategically important floral departments</p>
      <span class="btn btn--orange">LEARN MORE</span>
    </div>
  </div>
  <div class="contact">
    <h2 class="contact__title script">Contact Us</h2>
    <p class="contact__copy">Lorem ipsum dolor sit ameted consectetur adipiscing elited sed do eiusmod tempor incididunt ut labore dolore magna aliqua Uted enim ad minim veniam, quis nostrud exercitation ullamco laboris nisi ut aliquip ex ea commodo consequat. Duis aute irure dolor in reprehenderit in voluptate velit esse cillum dolore</p>
    <div class="contact__actions"><span class="btn btn--orange">NEW FLORIST FRANCHISE INQUIRY</span><span class="btn btn--outline">PROFESSIONAL FLORIST FRANCHISE INQUIRY</span></div>
    <svg class="wave" style="bottom:0" height="34" viewBox="0 0 301 34"><path d="M0 18 C50 4 110 6 170 16 C230 26 270 20 301 10 L301 34 L0 34Z" fill="#f0961c"/><path d="M0 24 C50 10 110 12 170 22 C230 30 270 26 301 16 L301 34 L0 34Z" fill="#12913f"/><path d="M0 30 C50 16 110 18 170 27 C230 34 270 30 301 22 L301 34 L0 34Z" fill="#fff"/></svg>
  </div>
  <div class="gallery">
    <h2 class="gallery__title script">Our Gallery</h2>
    <div class="gallery__row gallery__row--top">
      <div class="hex" style="background:linear-gradient(#6f8a4a,#5a3a2a)" role="img" aria-label="Florist standing in shop"></div>
      <div class="hex" style="background:linear-gradient(#d86a9a,#4e6e3a)" role="img" aria-label="Florist holding bouquet"></div>
      <div class="hex" style="background:linear-gradient(#f0b8a0,#d84a6a)" role="img" aria-label="Florist with pink flowers"></div>
      <div class="hex" style="background:linear-gradient(#5a6a3a,#a03a3a)" role="img" aria-label="Florists arranging flowers"></div>
    </div>
    <div class="gallery__row gallery__row--bottom">
      <div class="hex" style="background:linear-gradient(#d8b0a0,#8a5a3a)" role="img" aria-label="Florist at counter"></div>
      <div class="hex" style="background:linear-gradient(#b0205a,#e86aa0)" role="img" aria-label="Pink flower box arrangement"></div>
      <div class="hex" style="background:linear-gradient(#e8d8d0,#5a6a4a)" role="img" aria-label="Hands arranging protea bouquet"></div>
    </div>
    <div class="deco" style="left:8px;top:110px;width:40px;height:56px;background:linear-gradient(#f0961c,#12913f)" role="img" aria-label="Decorative honeycomb flower illustration"></div>
    <div class="deco" style="right:4px;top:76px;width:26px;height:80px;background:linear-gradient(#12913f,#f0961c)" role="img" aria-label="Decorative bee illustration"></div>
  </div>
  <footer class="site-footer">
    <svg class="wave" style="top:-12px" height="40" viewBox="0 0 301 40"><path d="M0 0 L301 0 L301 6 C250 24 150 26 90 12 C50 4 20 6 0 12Z" fill="#fff"/><path d="M0 12 C20 6 50 4 90 12 C150 26 250 24 301 6 L301 14 C250 32 150 32 90 18 C50 10 20 12 0 18Z" fill="#f0961c"/><path d="M0 18 C20 12 50 10 90 18 C150 32 250 32 301 14 L301 18 C250 36 150 36 90 22 C50 14 20 16 0 22Z" fill="#12913f"/></svg>
    <div class="footer__brand"><span class="brand__dot"></span><span class="brand__name">Lantern Petals</span></div>
    <div class="footer__col footer__col--links"><h4>QUICK LINKS</h4><ul><li>» &nbsp;Home</li><li>» &nbsp;About</li><li>» &nbsp;For Supermarkets</li><li>» &nbsp;For Franchisees</li><li>» &nbsp;Contact</li></ul></div>
    <div class="footer__col footer__col--contact"><h4>CONTACT US</h4><div class="contact-line"><i></i><b>+ 1.555.010.2040</b></div><div class="contact-line"><i></i>hello@lanternpetals.com</div><div class="contact-line"><i></i>114 Orchard Lane suite four near the market</div><div class="contact-line"><i></i><u>View Other Locations</u></div></div>
    <div class="footer__col footer__col--subscribe"><h4>SUBSCRIBE NOW</h4><p>Sign up to our newsletter and stay up to date</p><div class="subscribe-field"><span>Email Address</span><b></b></div><div class="footer__social"><i></i><i></i></div></div>
    <div class="footer__bar">© 2024 Lantern Petals. All Rights Reserved</div>
  </footer>
</section>

</div>
</body>
</html>
```